"Harbor Builders" is a residential building company and needs a new business card design and may re

We would like a redesign based on the existing logo, and would like to see a new font as well. We are bespoke home builders who build sustainable energy efficient homes.

Industry/Entity Type

Construction

Contact Information for Business Card

Business card size 40mm x 90mm

Colors

Designer to choose colors to be used in the design.

```html
<!DOCTYPE html>
<html lang="en">
<head>
<meta charset="utf-8">
<title>Harbor Builders — Business Card</title>
<link rel="stylesheet" href="https://fonts.googleapis.com/css2?family=Roboto:wght@400;500;700&family=Roboto+Condensed:wght@700&display=swap">
<style>
  :root {
    --lime: #bcd631;
    --ink: #1b1b1c;
    --paper: #f3f3f3;
    --backdrop: #e6e1d9;
    --white: #ffffff;
  }
  * { margin: 0; padding: 0; box-sizing: border-box; }
  html, body { width: 1200px; height: 960px; overflow: hidden; }
  body {
    background: var(--backdrop);
    font-family: "Roboto", Arial, sans-serif;
    color: var(--ink);
    position: relative;
  }
  .card { position: absolute; overflow: hidden; }

  /* Front */
  .card-front {
    left: 302px; top: 128px; width: 602px; height: 344px;
    background: var(--lime);
  }
  .front-bg { position: absolute; inset: 0; }
  .brand {
    position: absolute;
    font-family: "Roboto", Arial, sans-serif;
    font-weight: 500;
    white-space: nowrap;
  }
  .card-front .brand {
    left: 0; right: 0; top: 42px; text-align: center;
    font-size: 38px; color: var(--lime);
  }
  .brand-mark {
    display: inline-block; width: 26px; height: 26px;
    background: currentColor; margin-right: 14px; vertical-align: -2px;
  }
  .holder-name {
    position: absolute; left: 0; right: 0; top: 186px; text-align: center;
    font-family: "Roboto Condensed", "Arial Narrow", sans-serif;
    font-weight: 700; font-size: 20px; letter-spacing: 0.3px;
  }
  .rule {
    position: absolute; left: 31px; top: 214px; width: 539px; height: 1px;
    background: var(--ink); opacity: 0.7;
  }
  .details, .address {
    position: absolute; list-style: none; font-size: 14px; line-height: 19px;
  }
  .details { left: 31px; top: 222px; }
  .details .gap { margin-top: 5px; }
  .details svg { width: 12px; height: 12px; margin-right: 9px; vertical-align: -1px; }
  .address { right: 32px; top: 251px; text-align: right; line-height: 18.5px; }
  .address .company { font-weight: 500; }

  /* Back */
  .card-back {
    left: 298px; top: 488px; width: 602px; height: 342px;
    background: var(--paper);
  }
  .card-back .brand {
    left: 0; right: 0; top: 138px; text-align: center;
    font-size: 44px; color: var(--ink);
  }
  .web-band {
    position: absolute; left: 0; right: 0; top: 295px; height: 25px;
    background: var(--ink); color: var(--white);
    font-size: 14px; letter-spacing: 3px; text-align: center; line-height: 25px;
  }
</style>
</head>
<body>
  <section class="card card-front" aria-label="Business card front">
    <svg class="front-bg" viewBox="0 0 602 344" width="602" height="344" aria-hidden="true">
      <polygon points="0,0 602,0 602,96 301,169 0,96" fill="var(--ink)"/>
    </svg>
    <div class="brand"><span class="brand-mark"></span>Harbor Builders</div>
    <h1 class="holder-name">DANIEL MARSH</h1>
    <div class="rule"></div>
    <ul class="details">
      <li>Registration 40218</li>
      <li>ABN: 12 345 678 901</li>
      <li class="gap"><svg viewBox="0 0 12 12"><rect x="3" y="0.5" width="6" height="11" rx="1" fill="none" stroke="currentColor" stroke-width="1.4"/><rect x="5" y="9" width="2" height="1" fill="currentColor"/></svg>0400 555 018</li>
      <li><svg viewBox="0 0 12 12"><rect x="0.5" y="2.5" width="11" height="7" fill="currentColor"/><polyline points="0.5,2.5 6,7 11.5,2.5" fill="none" stroke="var(--lime)" stroke-width="1"/></svg>daniel@harborbuilders.com.au</li>
      <li><svg viewBox="0 0 12 12"><circle cx="6" cy="6" r="5.5" fill="currentColor"/><ellipse cx="6" cy="6" rx="2.2" ry="5.5" fill="none" stroke="var(--lime)" stroke-width="0.8"/><line x1="0.5" y1="6" x2="11.5" y2="6" stroke="var(--lime)" stroke-width="0.8"/></svg>www.harborbuilders.com.au</li>
    </ul>
    <ul class="address">
      <li class="company">Harbor Builders Pty Ltd</li>
      <li>PO Box 4120</li>
      <li>Eastgate</li>
      <li>LPO Bayside WA 6999</li>
    </ul>
  </section>

  <section class="card card-back" aria-label="Business card back">
    <div class="brand"><span class="brand-mark"></span>Harbor Builders</div>
    <div class="web-band">www.harborbuilders.com.au</div>
  </section>
</body>
</html>
```